Consumer and commercial IOT solutions (Internet Of Things)

We are a startup and are looking for business cards with logo. The logo will appear on all of our media as well as our ecommerce site and social sites that have yet to be developed. We want to present a fresh face on a high tech company that innovates at every turn. You can read about our solutions on our information only web site www.plonaxhub.net - We have some wording we would like used on our business cards but there is no place for this except for here. The company name is "RM Industrial IOT" I have some samples of logos I am interested in seeing but I will let your team make the initial presentations

```html
<!DOCTYPE html>
<html lang="en">
<head>
<meta charset="utf-8">
<title>RM Industrial IOT — Business Card</title>
<link rel="stylesheet" href="https://fonts.googleapis.com/css2?family=Montserrat:wght@400;500;600;700&display=swap">
<style>
  :root {
    --page-bg: #e9e7e4;
    --card-dark: #1e2023;
    --card-dark-2: #33373c;
    --card-light: #ffffff;
    --accent: #f26a1b;
    --navy: #1b2a45;
    --ink: #2b2f36;
    --white: #ffffff;
  }
  * { box-sizing: border-box; margin: 0; padding: 0; }
  html, body {
    width: 1200px; height: 900px; overflow: hidden;
    background: var(--page-bg);
    font-family: "Montserrat", sans-serif;
  }
  .canvas { position: relative; width: 1200px; height: 900px; }
  .card {
    position: absolute; left: 290px;
    width: 620px; height: 354px;
    border-radius: 22px;
    overflow: hidden;
    box-shadow: 0 14px 30px rgba(0,0,0,0.18);
  }
  /* Front */
  .card-front { top: 74px; background: var(--card-dark); }
  .front-photo {
    position: absolute; inset: 0;
    background:
      radial-gradient(ellipse at 62% 40%, rgba(120,90,70,0.45) 0%, rgba(60,55,55,0.25) 35%, transparent 65%),
      linear-gradient(135deg, var(--card-dark) 0%, var(--card-dark-2) 55%, var(--card-dark) 100%);
  }
  .front-content {
    position: absolute; inset: 0;
    display: flex; align-items: center; justify-content: center; gap: 26px;
  }
  .front-mark {
    width: 44px; height: 44px; border-radius: 50%;
    background: var(--accent); flex: none;
  }
  .divider { width: 2px; height: 110px; background: var(--accent); flex: none; }
  .company-name {
    color: var(--white);
    font-weight: 600;
    font-size: 32px;
    line-height: 1.2;
    letter-spacing: 0.01em;
    white-space: nowrap;
  }
  /* Back */
  .card-back { top: 472px; background: var(--card-light); }
  .back-content {
    position: absolute; inset: 0;
    display: flex; align-items: center; justify-content: center; gap: 34px;
  }
  .brand-lockup { display: flex; align-items: center; gap: 12px; }
  .brand-dot {
    width: 22px; height: 22px; border-radius: 50%; background: var(--accent); flex: none;
  }
  .brand-name {
    color: var(--navy); font-weight: 600; font-size: 19px; line-height: 1.2;
    white-space: nowrap;
  }
  .back-content .divider { height: 130px; }
  .person-name {
    font-weight: 700; font-size: 20px; letter-spacing: 0.02em;
    text-transform: uppercase; color: var(--navy);
  }
  .person-name .surname { color: var(--accent); }
  .person-role {
    font-size: 15px; font-weight: 500; color: var(--ink);
    text-transform: uppercase; letter-spacing: 0.04em; margin-top: 2px;
  }
  .contact-list { list-style: none; margin-top: 16px; }
  .contact-list li {
    display: flex; align-items: center; gap: 10px;
    font-size: 15px; color: var(--ink); line-height: 1.6;
  }
  .contact-list svg { width: 13px; height: 13px; flex: none; }
</style>
</head>
<body>
<main class="canvas">

  <section class="card card-front">
    <div class="front-photo" role="img" aria-label="Dark photo of a hand touching a glowing tech interface with faint IoT icons"></div>
    <div class="front-content">
      <div class="front-mark"></div>
      <div class="divider"></div>
      <h1 class="company-name">RM Industrial IOT</h1>
    </div>
  </section>

  <section class="card card-back">
    <div class="back-content">
      <div class="brand-lockup">
        <span class="brand-dot"></span>
        <span class="brand-name">RM Industrial IOT</span>
      </div>
      <div class="divider"></div>
      <div class="contact-block">
        <p class="person-name">Dorian <span class="surname">Kessler</span></p>
        <p class="person-role">Co-Founder &amp; CEO</p>
        <ul class="contact-list">
          <li>
            <svg viewBox="0 0 16 16" aria-hidden="true"><path fill="#f26a1b" d="M3.6 1.2l2.3 2.6-1.2 1.9c.9 1.9 2.3 3.3 4.2 4.2l1.9-1.2 2.6 2.3-1.3 2.3C7 13.7 2.3 9 1.2 3.4z"/></svg>
            <span>0491570118</span>
          </li>
          <li>
            <svg viewBox="0 0 16 16" aria-hidden="true"><rect x="1.5" y="3.5" width="13" height="9" fill="none" stroke="#f26a1b" stroke-width="1.5"/><path d="M1.5 3.5L8 9l6.5-5.5" fill="none" stroke="#f26a1b" stroke-width="1.5"/></svg>
            <span>info@plonaxhub.com</span>
          </li>
          <li>
            <svg viewBox="0 0 16 16" aria-hidden="true"><circle cx="8" cy="8" r="6.5" fill="none" stroke="#f26a1b" stroke-width="1.5"/><path d="M1.5 8h13M8 1.5c-2.6 3.6-2.6 9.4 0 13M8 1.5c2.6 3.6 2.6 9.4 0 13" fill="none" stroke="#f26a1b" stroke-width="1.2"/></svg>
            <span>www.plonaxhub.net</span>
          </li>
        </ul>
      </div>
    </div>
  </section>

</main>
</body>
</html>
```